Pellowar

We need logo and wesbsite for a software development company based out of Hyderabad, India focused on startups and mid sized companies focused on build a new software products in USA and Europe countires.

Target Market(s)

startup and midsized companies in teh USA and Europe for software product development.

Industry/Entity Type

software development

Coding

Coded - Design and coding required

Number of Pages Required

5+ page

Requirements
Must have
• latest design concepts and very elegant
Nice to have
• each page should have images that reflects the content
Should not have
• too many colors

```html
<!DOCTYPE html>
<html lang="en">
<head>
<meta charset="utf-8">
<title>Pellowar — Software Product Development</title>
<link href="https://fonts.googleapis.com/css2?family=Poppins:wght@400;500;600&family=Lato:wght@400;700&display=swap" rel="stylesheet">
<style>
:root{
  --orange:#e85a1e;
  --orange-soft:#f07a3e;
  --blue:#1f86d2;
  --ink:#222a33;
  --text:#444c55;
  --muted:#6b727a;
  --grey-bg:#f0f1f3;
  --white:#fff;
}
*{box-sizing:border-box;margin:0;padding:0}
html,body{width:1200px;height:3955px;overflow:hidden;background:var(--white)}
body{position:relative;font-family:"Lato",sans-serif;color:var(--text)}
.abs{position:absolute}
.head{font-family:"Poppins",sans-serif}
.btn{position:absolute;display:flex;align-items:center;justify-content:center;border-radius:30px;font-family:"Poppins",sans-serif;font-weight:500;font-size:15px;color:var(--white);background:var(--orange);letter-spacing:.2px}
.btn-outline{background:var(--white);color:var(--ink);border:2px solid var(--orange)}
.ph{position:absolute}
.section-title{position:absolute;font-family:"Poppins",sans-serif;font-weight:500;font-size:34px;color:var(--orange);letter-spacing:.5px}
.centered{left:0;width:1200px;text-align:center}

/* top bar */
.topbar{left:0;top:0;width:1200px;height:31px;background:var(--blue);color:var(--white);font-size:14px}
.topbar .mail{left:110px;top:6px;display:flex;gap:8px;align-items:center}
.topbar .phone{right:110px;top:6px;display:flex;gap:8px;align-items:center}
/* nav */
.nav{top:31px;left:0;width:1200px;height:67px;border-bottom:1px solid #e6e6e6}
.nav-links{left:110px;top:24px;display:flex;gap:29px;font-size:15px;color:var(--ink)}
.nav-links .active{border-bottom:2px solid var(--orange);padding-bottom:4px}
.brand{left:0;width:1200px;top:16px;text-align:center;font-family:"Poppins",sans-serif;font-weight:500;font-size:29px;color:var(--orange);letter-spacing:.5px}
.lang{left:869px;top:20px;display:flex;align-items:center;gap:8px;font-family:"Poppins",sans-serif;font-weight:600;font-size:14px;color:var(--ink)}
.lang .dot{width:28px;height:28px;border-radius:50%;background:#3d5aa8}
/* hero */
.hero-title{left:110px;top:240px;font-family:"Poppins",sans-serif;font-weight:600;font-size:46px;line-height:52px;color:var(--white)}
.hero-sub{left:110px;top:356px;font-family:"Poppins",sans-serif;font-weight:500;font-size:19px;line-height:29px;color:var(--white)}
.dots{left:48px;top:343px;display:flex;flex-direction:column;gap:10px}
.dots i{width:10px;height:10px;border-radius:50%;background:var(--white);display:block}
.dots i:first-child{background:var(--orange)}
/* about */
.about-title{left:622px;top:830px}
.about-lead{left:622px;top:882px;width:500px;font-family:"Poppins",sans-serif;font-size:20px;line-height:30px;color:var(--ink)}
.checks{left:622px;top:964px;list-style:none;font-size:15.5px;color:var(--ink)}
.checks li{display:flex;align-items:center;gap:20px;height:42.5px}
/* product band */
.band{left:0;top:1332px;width:1200px;height:590px;background:var(--orange)}
.band-title{top:1384px;color:var(--white)}
.band-desc{top:1436px;font-size:15px;line-height:22px;color:#fde6da}
.pcard{position:absolute;top:1512px;width:288px;height:342px;background:var(--white);text-align:center}
.pcard .ico{position:absolute;left:106px;top:46px}
.pcard h3{position:absolute;top:160px;left:0;width:100%;font-family:"Poppins",sans-serif;font-weight:500;font-size:22px;color:var(--orange)}
.pcard p{position:absolute;top:200px;left:30px;width:228px;font-size:15px;line-height:22px;color:var(--ink)}
.pcard .btn{left:55px;top:265px;width:168px;height:43px}
/* case study */
.case-title{left:110px;top:2012px}
.case-text{left:110px;top:2072px;width:413px;font-size:15px;line-height:22.4px;text-align:justify;color:var(--ink)}
/* team */
.team-bg{left:0;top:2421px;width:1200px;height:534px;background:var(--grey-bg)}
.tcard{position:absolute;top:2568px;width:263px;height:298px;background:var(--white);text-align:center}
.tcard .ring{position:absolute;left:80px;top:27px;width:103px;height:103px;border:2px solid var(--orange);border-radius:50%;display:flex;align-items:center;justify-content:center}
.tcard .num{position:absolute;left:119px;top:118px;width:24px;height:24px;border-radius:50%;background:var(--orange);color:var(--white);font-size:13px;font-family:"Poppins",sans-serif;display:flex;align-items:center;justify-content:center}
.tcard h3{position:absolute;top:164px;width:100%;font-family:"Poppins",sans-serif;font-weight:500;font-size:18.5px;color:var(--ink)}
.tcard p{position:absolute;top:200px;left:30px;width:203px;font-size:14.5px;line-height:22px;color:var(--muted)}
.tcard .link{position:absolute;top:254px;left:0;width:100%;font-family:"Poppins",sans-serif;font-size:17px;color:var(--orange)}
.tcard .link span{border-bottom:2px solid var(--orange);padding-bottom:2px}
/* blog */
.blog-desc{top:3088px;font-size:15.5px;line-height:26px;color:var(--ink)}
.post{position:absolute;top:3159px;width:315px}
.post .ph{position:relative;width:315px;height:203px}
.post .date{margin:20px 0 0 18px;font-family:"Poppins",sans-serif;font-size:14.5px;font-weight:500;color:var(--orange)}
.post h4{margin:12px 0 0 16px;font-family:"Poppins",sans-serif;font-weight:400;font-size:19px;line-height:26px;color:var(--ink)}
.post .link{margin:16px 0 0 16px;font-family:"Poppins",sans-serif;font-size:15px;color:var(--orange);display:inline-block;border-bottom:1.5px solid var(--orange)}
/* footer */
.footer{left:0;top:3592px;width:1200px;height:363px}
.f-brand{left:107px;top:3704px;font-family:"Poppins",sans-serif;font-weight:500;font-size:30px;color:var(--white)}
.f-about{left:110px;top:3750px;width:240px;font-size:15px;line-height:22px;color:#e3efff}
.f-col{top:3703px;color:var(--white)}
.f-col h5{font-family:"Poppins",sans-serif;font-weight:500;font-size:19px;margin-bottom:10px}
.f-col ul{list-style:none;font-size:15px;line-height:22px;color:#e3efff}
.f-input{left:795px;top:3773px;width:287px;height:36px;border-radius:20px;background:var(--white);font-size:14px;color:#9aa0a6;padding:10px 22px}
.f-line{left:110px;top:3890px;width:980px;height:1px;background:#7fb5e4}
.f-copy{top:3918px;font-size:15px;color:#e3efff}
</style>
</head>
<body>

<!-- top bar -->
<div class="abs topbar">
  <div class="abs mail">
    <svg width="22" height="16" viewBox="0 0 22 16"><rect x="1" y="1" width="20" height="14" fill="none" stroke="#fff" stroke-width="1.6"/><path d="M1 1 L11 9 L21 1" fill="none" stroke="#fff" stroke-width="1.6"/></svg>
    info@pellowar.com
  </div>
  <div class="abs phone">
    <svg width="16" height="16" viewBox="0 0 24 24"><path fill="#fff" d="M6.6 10.8a15 15 0 0 0 6.6 6.6l2.2-2.2c.3-.3.7-.4 1-.2 1.1.4 2.3.6 3.6.6.6 0 1 .4 1 1V20c0 .6-.4 1-1 1A17 17 0 0 1 3 4c0-.6.4-1 1-1h3.5c.6 0 1 .4 1 1 0 1.3.2 2.5.6 3.6.1.3 0 .7-.2 1z"/></svg>
    +1(555) 010 2040
  </div>
  <svg class="abs" style="left:540px;top:6px" width="120" height="26" viewBox="0 0 120 26"><path d="M0 26 L60 0 L120 26Z" fill="#fff"/></svg>
</div>

<!-- navigation -->
<div class="abs nav">
  <nav class="abs nav-links">
    <span class="active">Home</span><span>About</span><span>Product</span><span>Team</span><span>Blog</span>
  </nav>
  <div class="abs brand">PELLOWAR</div>
  <div class="abs lang"><span class="dot"></span>EN
    <svg width="10" height="8" viewBox="0 0 10 8"><path d="M1 2 L5 6 L9 2" fill="none" stroke="#222" stroke-width="1.5"/></svg>
  </div>
  <div class="btn" style="left:969px;top:16px;width:119px;height:37px;font-size:15px">LOGIN</div>
</div>

<!-- hero -->
<div class="ph" role="img" aria-label="Two smiling colleagues discussing ideas in a bright office" style="left:0;top:98px;width:1200px;height:610px;background:linear-gradient(100deg,#2f3236 0%,#55575a 40%,#8a7f74 65%,#b9b2a8 100%)"></div>
<svg class="abs" style="left:0;top:640px" width="1200" height="80" viewBox="0 0 1200 80">
  <path d="M0 10 L600 64 L1200 4 L1200 80 L0 80Z" fill="var(--orange)"/>
  <path d="M0 16 L600 72 L1200 10 L1200 80 L0 80Z" fill="#fff"/>
</svg>
<div class="abs dots"><i></i><i></i><i></i></div>
<h1 class="abs hero-title">Welcome To<br>The Pellowar</h1>
<p class="abs hero-sub">Building software products or<br>solutions is changing day by day</p>
<div class="btn" style="left:110px;top:434px;width:209px;height:51px;font-size:16px">GET STARTED</div>

<!-- about -->
<svg class="abs" style="left:96px;top:776px" width="475" height="468" viewBox="0 0 475 468">
  <path d="M4 200 V4 H204" fill="none" stroke="var(--orange)" stroke-width="2.5" stroke-dasharray="8 6"/>
  <path d="M470 265 V465 H270" fill="none" stroke="var(--orange)" stroke-width="2.5" stroke-dasharray="8 6"/>
</svg>
<div class="ph" role="img" aria-label="Two developers reviewing work together on a laptop" style="left:112px;top:792px;width:442px;height:442px;background:linear-gradient(135deg,#c9c2b8,#6f6a66 60%,#3c3d40);border:2px solid #fff;outline:1px solid #ddd"></div>
<h2 class="section-title about-title">ABOUT US</h2>
<p class="abs about-lead">Teams are the essence of every business. They can create wonders if built with perfectio</p>
<ul class="abs checks">
  <li><svg width="30" height="26" viewBox="0 0 30 26"><path d="M22 6 A11 11 0 1 0 24 14" fill="none" stroke="var(--orange)" stroke-width="2.5" stroke-linecap="round"/><path d="M7 12 L12 17 L27 3" fill="none" stroke="var(--orange)" stroke-width="2.5" stroke-linecap="round"/></svg>Brainstorm for a product that will solve a problem</li>
  <li><svg width="30" height="26" viewBox="0 0 30 26"><path d="M22 6 A11 11 0 1 0 24 14" fill="none" stroke="var(--orange)" stroke-width="2.5" stroke-linecap="round"/><path d="M7 12 L12 17 L27 3" fill="none" stroke="var(--orange)" stroke-width="2.5" stroke-linecap="round"/></svg>Incorporate ideas from business partners or stakeholders</li>
  <li><svg width="30" height="26" viewBox="0 0 30 26"><path d="M22 6 A11 11 0 1 0 24 14" fill="none" stroke="var(--orange)" stroke-width="2.5" stroke-linecap="round"/><path d="M7 12 L12 17 L27 3" fill="none" stroke="var(--orange)" stroke-width="2.5" stroke-linecap="round"/></svg>Outsource the development team</li>
  <li><svg width="30" height="26" viewBox="0 0 30 26"><path d="M22 6 A11 11 0 1 0 24 14" fill="none" stroke="var(--orange)" stroke-width="2.5" stroke-linecap="round"/><path d="M7 12 L12 17 L27 3" fill="none" stroke="var(--orange)" stroke-width="2.5" stroke-linecap="round"/></svg>8.Sell the product to the target market</li>
</ul>
<div class="btn" style="left:626px;top:1147px;width:165px;height:42px">LEARN MORE</div>

<!-- build your product -->
<div class="abs band"></div>
<h2 class="section-title centered band-title" style="color:#fff">BUILD YOUR PRODUCT</h2>
<p class="abs centered band-desc">As startups are racing to build software as a product, they have stumbling blocks on building<br>software from scratch. One of the reasons is stiff competition.</p>
<svg class="abs" style="left:40px;top:1650px" width="30" height="48" viewBox="0 0 30 48"><path d="M24 4 L6 24 L24 44" fill="none" stroke="#fff" stroke-width="5" stroke-linecap="round"/></svg>
<svg class="abs" style="left:1132px;top:1650px" width="30" height="48" viewBox="0 0 30 48"><path d="M6 4 L24 24 L6 44" fill="none" stroke="#fff" stroke-width="5" stroke-linecap="round"/></svg>
<svg class="abs" style="left:402px;top:1646px" width="54" height="44" viewBox="0 0 54 44"><path d="M4 6 H46 M40 2 L46 6 L40 10" fill="none" stroke="#fff" stroke-width="1.5" stroke-dasharray="4 3"/><circle cx="20" cy="26" r="10" fill="none" stroke="#fff" stroke-width="1.5" stroke-dasharray="4 3"/></svg>
<svg class="abs" style="left:747px;top:1646px" width="54" height="44" viewBox="0 0 54 44"><path d="M4 6 H46 M40 2 L46 6 L40 10" fill="none" stroke="#fff" stroke-width="1.5" stroke-dasharray="4 3"/><circle cx="20" cy="26" r="10" fill="none" stroke="#fff" stroke-width="1.5" stroke-dasharray="4 3"/></svg>

<div class="pcard" style="left:112px">
  <svg class="ico" width="90" height="92" viewBox="0 0 90 92" fill="none" stroke="#222" stroke-width="2.5"><circle cx="30" cy="22" r="14"/><path d="M4 88 V70 a26 20 0 0 1 52 0 V88 Z"/><rect x="54" y="10" width="32" height="26" stroke="var(--orange)"/><circle cx="68" cy="68" r="12"/><circle cx="68" cy="68" r="5" stroke="var(--orange)"/></svg>
  <h3>Project Manager</h3>
  <p>Identify the issue and conduct interviews with possible users to</p>
  <div class="btn btn-outline">LEARN MORE</div>
</div>
<div class="pcard" style="left:456px">
  <svg class="ico" width="90" height="92" viewBox="0 0 90 92" fill="none" stroke="#222" stroke-width="2.5"><circle cx="45" cy="46" r="18" stroke="var(--orange)"/><circle cx="12" cy="12" r="7"/><circle cx="78" cy="12" r="7"/><circle cx="12" cy="74" r="7"/><circle cx="78" cy="74" r="7"/><path d="M22 12 H68 M22 74 H68" stroke-dasharray="3 3"/><path d="M2 30 h20 M68 30 h20 M2 90 h20 M68 90 h20"/></svg>
  <h3>Team Lead</h3>
  <p>Identify the issue and conduct interviews with possible users to</p>
  <div class="btn btn-outline">LEARN MORE</div>
</div>
<div class="pcard" style="left:801px">
  <svg class="ico" width="90" height="92" viewBox="0 0 90 92" fill="none" stroke="#222" stroke-width="2.5"><circle cx="45" cy="24" r="18"/><path d="M6 88 V76 a39 24 0 0 1 78 0 V88 Z"/><rect x="24" y="52" width="42" height="30" fill="#fff" stroke="var(--orange)"/><path d="M38 62 l-5 5 5 5 M52 62 l5 5 -5 5 M47 60 l-4 14" stroke="var(--orange)"/></svg>
  <h3>Developers</h3>
  <p>Identify the issue and conduct interviews with possible users to</p>
  <div class="btn btn-outline">LEARN MORE</div>
</div>

<!-- case study -->
<h2 class="section-title case-title">CASE STUDY</h2>
<p class="abs case-text">Many business owners have great ideas but no experience with the actual product. Once you have an idea in mind, you will require software development aid at some point – whether your concept is for next-generation software or an inventive approach to offering an existing service. It might also be the development of a mobile app or web-based software. Whatever product you're working on, you'll need a technical co-founder to help you get it off the ground. An</p>
<div class="btn" style="left:110px;top:2276px;width:166px;height:42px">LEARN MORE</div>
<svg class="abs" style="left:588px;top:1997px" width="510" height="348" viewBox="0 0 510 348">
  <path d="M2 150 V2 H202" fill="none" stroke="var(--orange)" stroke-width="2.5" stroke-dasharray="8 6"/>
  <path d="M508 140 V346 H308" fill="none" stroke="var(--orange)" stroke-width="2.5" stroke-dasharray="8 6"/>
</svg>
<div class="ph" role="img" aria-label="Developer coding at a desk with multiple monitors" style="left:599px;top:2008px;width:488px;height:325px;background:linear-gradient(120deg,#0f2540,#1f4a78 45%,#2a3440 80%,#151a20);border:3px solid #fff;outline:1px solid #ddd"></div>

<!-- build your team -->
<div class="abs team-bg"></div>
<h2 class="section-title centered" style="top:2494px">BUILD YOUR TEAM</h2>

<div class="tcard" style="left:34px">
  <div class="ring"><svg width="58" height="52" viewBox="0 0 58 52" fill="none" stroke="#222" stroke-width="2"><circle cx="14" cy="14" r="9"/><rect x="30" y="4" width="24" height="16" stroke="var(--orange)"/><path d="M4 48 v-10 a10 8 0 0 1 20 0 v10"/><circle cx="42" cy="38" r="8"/></svg></div>
  <div class="num">1</div>
  <h3>Pass cognitive aptitude</h3>
  <p>Accepting job applications from the entire world</p>
  <div class="link"><span>LEAN MORE</span></div>
</div>
<div class="tcard" style="left:322px">
  <div class="ring"><svg width="58" height="52" viewBox="0 0 58 52" fill="none" stroke="#222" stroke-width="2"><path d="M8 46 L48 8" stroke="var(--orange)"/><path d="M40 6 L50 6 L50 16" stroke="var(--orange)"/><circle cx="22" cy="20" r="5"/><path d="M16 34 l10 -6 8 8"/><circle cx="10" cy="40" r="5"/></svg></div>
  <div class="num">2</div>
  <h3>Pass English proficiency</h3>
  <p>Accepting job applications from the entire world</p>
  <div class="link"><span>LEAN MORE</span></div>
</div>
<div class="tcard" style="left:609px">
  <div class="ring"><svg width="58" height="52" viewBox="0 0 58 52" fill="none" stroke="#222" stroke-width="2"><circle cx="29" cy="18" r="7"/><path d="M17 46 v-8 a12 8 0 0 1 24 0 v8"/><circle cx="8" cy="20" r="4" stroke="var(--orange)"/><circle cx="50" cy="20" r="4" stroke="var(--orange)"/><circle cx="29" cy="4" r="3" stroke="var(--orange)"/></svg></div>
  <div class="num">3</div>
  <h3>Prove real world job skills</h3>
  <p>Accepting job applications from the entire world</p>
  <div class="link"><span>LEAN MORE</span></div>
</div>
<div class="tcard" style="left:898px">
  <div class="ring"><svg width="58" height="52" viewBox="0 0 58 52" fill="none" stroke="#222" stroke-width="2"><circle cx="18" cy="16" r="8"/><path d="M6 48 v-12 a12 9 0 0 1 24 0 v12"/><path d="M34 8 h20 M34 18 h20 M34 28 h14" stroke="var(--orange)"/></svg></div>
  <div class="num">4</div>
  <h3>Pass cognitive aptitude</h3>
  <p>Accepting job applications from the entire world</p>
  <div class="link"><span>LEAN MORE</span></div>
</div>

<!-- latest blog -->
<h2 class="section-title centered" style="top:3032px">LATEST BLOG</h2>
<p class="abs centered blog-desc">Amet, Consectetur, Adipisci Velit, Sed Quia Non Numquam Eius Modi Tempora Incidunt Ut Labore Et Dolore<br>Magnam Aliquam Quaerat Voluptatem. Ut Enim Ad Minima Veniam, Quis Nostrum Exercita</p>

<article class="post" style="left:110px">
  <div class="ph" role="img" aria-label="Team member presenting designs on a large monitor" style="background:linear-gradient(120deg,#3a3e44,#8f9aa6 55%,#d8dee6)"></div>
  <div class="date">JULY 1, 2019</div>
  <h4>Quis Nostrum Exercitationem<br>Ullam Corporis Suscipit</h4>
  <div class="link">LEARN MORE</div>
</article>
<article class="post" style="left:443px">
  <div class="ph" role="img" aria-label="Programmer working with code on screens in a dark room" style="background:linear-gradient(120deg,#0d2f5c,#1c5fa0 50%,#1a2230)"></div>
  <div class="date">MARCH 14, 2019</div>
  <h4>uia Dolor Sit Amet<br>Consectetur Adipisci Velit</h4>
  <div class="link">LEARN MORE</div>
</article>
<article class="post" style="left:777px">
  <div class="ph" role="img" aria-label="Colleagues working together at computers in an open office" style="background:linear-gradient(120deg,#e7e6e2,#8b8781 50%,#3e3b38)"></div>
  <div class="date">OCTOBER 1, 2018</div>
  <h4>Quia Voluptas SiAspern<br>atur Aut Odit Aut Fugit Sed</h4>
  <div class="link">LEARN MORE</div>
</article>

<!-- footer -->
<svg class="abs footer" width="1200" height="363" viewBox="0 0 1200 363">
  <path d="M0 62 L600 0 L1200 62 V363 H0Z" fill="var(--orange)"/>
  <path d="M0 72 L600 12 L1200 72 V363 H0Z" fill="var(--blue)"/>
</svg>
<div class="abs f-brand">PELLOWAR</div>
<p class="abs f-about">Businesses can focus on core activities of Sales and Marketing to achieve revenue growth, and we will accelerate in your</p>
<div class="abs f-col" style="left:414px"><h5>Helpful links</h5><ul><li>Home</li><li>About</li><li>Product</li><li>Team</li><li>Blog</li></ul></div>
<div class="abs f-col" style="left:600px"><h5>Product</h5><ul><li>Project Manager</li><li>Team Lead</li><li>Business analyst</li><li>Developers</li><li>Testers</li></ul></div>
<div class="abs f-col" style="left:797px"><h5>News Updates</h5><ul><li>emo Enim Ipsam Voluptatem</li></ul></div>
<div class="abs f-input">Email Address</div>
<div class="btn" style="left:795px;top:3819px;width:134px;height:37px;font-size:14px">SUBMIT</div>
<div class="abs f-line"></div>
<p class="abs centered f-copy">Copyrights@2022 Pellowar. All Rights Reserved.</p>

</body>
</html>
```